Keystone Trench Co Business Card*

Looking for a professional, clean and crisp business card

I am in the underground utilities industry and am just looking for a really impressive business card. I would like our card to be white with our symbol crisp and clear with it protruding. I also have a business partner that will require his name and info on the card once the design is set. I would like to have our website info on the card which is;
http://keystonetrenchco.example/

Contact Information for Business Card

Website, contact name, number and email

```html
<!DOCTYPE html>
<html lang="en">
<head>
<meta charset="utf-8">
<title>Keystone Trench Co — Business Card</title>
<link rel="stylesheet" href="https://fonts.googleapis.com/css2?family=Roboto+Condensed:wght@400;700&display=swap">
<style>
  :root {
    --page-bg: #e9e7e6;
    --card-bg: #ffffff;
    --band-blue: #3a62a8;
    --ink: #1f1f1f;
    --ink-soft: #2c2c2c;
    --accent-red: #e02b2b;
  }
  * { margin: 0; padding: 0; box-sizing: border-box; }
  html, body {
    width: 1200px;
    height: 900px;
    overflow: hidden;
    background: var(--page-bg);
    font-family: "Roboto Condensed", "Arial Narrow", sans-serif;
  }
  .canvas {
    position: relative;
    width: 1200px;
    height: 900px;
  }
  .business-card {
    position: absolute;
    left: 120px;
    top: 160px;
    width: 960px;
    height: 580px;
    background: var(--card-bg);
    box-shadow: 0 10px 30px rgba(0, 0, 0, 0.12);
    overflow: hidden;
  }
  .brand-band {
    position: absolute;
    left: 149px;
    top: 0;
    width: 124px;
    height: 100%;
    background: var(--band-blue);
  }
  .brand-seal {
    position: absolute;
    left: 58px;
    top: 134px;
    width: 312px;
    height: 312px;
    border-radius: 50%;
    background: var(--card-bg);
    display: flex;
    align-items: center;
    justify-content: center;
  }
  .brand-name {
    font-weight: 700;
    font-size: 40px;
    line-height: 1.05;
    letter-spacing: 1px;
    text-transform: uppercase;
    text-align: center;
    color: var(--ink);
  }
  .contact-block {
    position: absolute;
    left: 463px;
    top: 168px;
  }
  .person-name {
    font-weight: 700;
    font-size: 38px;
    line-height: 1;
    color: var(--ink);
    text-transform: uppercase;
  }
  .person-title {
    font-weight: 400;
    font-size: 29px;
    line-height: 1.15;
    color: var(--ink-soft);
  }
  .contact-list {
    list-style: none;
    margin-top: 64px;
  }
  .contact-item {
    display: flex;
    align-items: center;
    gap: 10px;
    font-size: 29px;
    line-height: 37px;
    color: var(--ink);
  }
  .contact-icon {
    width: 28px;
    height: 28px;
    flex: none;
  }
</style>
</head>
<body>
<main class="canvas">
  <section class="business-card" aria-label="Keystone Trench Co business card">
    <div class="brand-band"></div>
    <div class="brand-seal">
      <p class="brand-name">Keystone<br>Trench Co</p>
    </div>

    <div class="contact-block">
      <h1 class="person-name">Daniel Mercer</h1>
      <p class="person-title">Managing Director</p>

      <ul class="contact-list">
        <li class="contact-item">
          <svg class="contact-icon" viewBox="0 0 24 24" aria-hidden="true">
            <path d="M6.6 2.5l3 3.4-1.8 2.4a12 12 0 0 0 7.9 7.9l2.4-1.8 3.4 3-1.6 3.1c-.4.7-1.2 1-2 .8A19 19 0 0 1 2.7 6.1c-.2-.8.1-1.6.8-2z" fill="var(--accent-red)"/>
            <path d="M14 3.5a7 7 0 0 1 6.5 6.5M14 7a3.5 3.5 0 0 1 3 3" fill="none" stroke="var(--accent-red)" stroke-width="1.8" stroke-linecap="round"/>
          </svg>
          <span>044-555 018 273</span>
        </li>
        <li class="contact-item">
          <svg class="contact-icon" viewBox="0 0 24 24" aria-hidden="true">
            <rect x="2" y="5" width="20" height="14" fill="var(--accent-red)"/>
            <path d="M2 5l10 8 10-8M2 19l7.5-7M22 19l-7.5-7" fill="none" stroke="#fff" stroke-width="1.5"/>
          </svg>
          <span>info@keystonetrenchco.example</span>
        </li>
        <li class="contact-item">
          <svg class="contact-icon" viewBox="0 0 24 24" aria-hidden="true">
            <g fill="none" stroke="var(--accent-red)" stroke-width="1.8">
              <circle cx="12" cy="12" r="9.5"/>
              <ellipse cx="12" cy="12" rx="4.5" ry="9.5"/>
              <path d="M2.5 12h19M4 7h16M4 17h16"/>
            </g>
          </svg>
          <span>www.keystonetrenchco.example</span>
        </li>
      </ul>
    </div>
  </section>
</main>
</body>
</html>
```